Clear Plastic Card Design

I am looking to have a business card designed from my logo icon. I am looking to match the style of a different business card I have attached in the files.
Looking for a card that is plastic, with layers of transparency in the shape of my logo icon (also attached in the files) - not a circle like the other card. The winning design will incorporate the red icon logo on the front and back and include the charity's name, "Light for the Weary Souls" in the same or similar font, as well as an email and phone number. For now, use the email: email@lightfortheweary-mail.org and the phone number 555-382-7194.
We like how the sample business card has transparency, partial and full opacity layers and a matching color scheme. Files will need to be in vector so that our business card printing company can work with it.
UPDATE:
We've some excellent designs in, thank you everyone! I got an early review from the owner, and he requested a minor redirect to find his perfect design. He wants the design to stand out by NOT being a rectangle. Try instead a circle, square, or best yet - something that falls in the outline of the logo icon, either fully or partially. Thank you, everyone!
Light for the Weary Souls text should be incorporated as well as a phone and email.

```html
<!DOCTYPE html>
<html lang="en">
<head>
<meta charset="utf-8">
<title>Light for the Weary Souls – Business Card</title>
<link rel="stylesheet" href="https://fonts.googleapis.com/css2?family=Inter:wght@400;500&display=swap">
<style>
  :root {
    --backdrop: #e4e4e4;
    --card: #ffffff;
    --ink: #222222;
    --icon: #000000;
    --brand-red: #e0301e;
  }
  * { box-sizing: border-box; margin: 0; padding: 0; }
  html, body {
    width: 1175px;
    height: 1200px;
    overflow: hidden;
    background: var(--backdrop);
    font-family: "Inter", Arial, sans-serif;
  }
  .business-card {
    position: absolute;
    left: 227px;
    top: 235px;
    width: 720px;
    height: 730px;
    background: var(--card);
    border-radius: 48px;
  }
  .brand {
    position: absolute;
    top: 170px;
    left: 0;
    width: 100%;
    display: flex;
    align-items: center;
    justify-content: center;
    gap: 22px;
  }
  .brand-mark {
    width: 96px;
    height: 96px;
    background: var(--brand-red);
  }
  .brand-name {
    color: var(--brand-red);
    font-weight: 500;
    font-size: 38px;
    line-height: 1.15;
  }
  .contact-icons {
    position: absolute;
    top: 420px;
    left: 0;
    width: 100%;
    display: flex;
    align-items: center;
    justify-content: center;
    gap: 6px;
  }
  .contact-icons .rule {
    width: 30px;
    height: 2px;
    background: var(--icon);
    margin: 0 6px;
  }
  .contact-icons svg { width: 42px; height: 42px; display: block; }
  .contact-details {
    position: absolute;
    top: 490px;
    left: 0;
    width: 100%;
    list-style: none;
    text-align: center;
    color: var(--ink);
    font-size: 30px;
    line-height: 40px;
  }
</style>
</head>
<body>
  <main class="business-card">
    <div class="brand">
      <div class="brand-mark"></div>
      <div class="brand-name">Light for the<br>Weary Souls</div>
    </div>

    <div class="contact-icons">
      <span class="rule"></span>
      <svg viewBox="0 0 42 42" aria-label="Phone">
        <circle cx="21" cy="21" r="21" fill="var(--icon)"/>
        <path d="M14 11c1-1 2.5-1 3.2.2l2 3.3c.5.9.3 2-.5 2.6l-1.4 1.1c1.2 2.8 3.4 5 6.2 6.2l1.1-1.4c.6-.8 1.7-1 2.6-.5l3.3 2c1.2.7 1.2 2.2.2 3.2l-1.6 1.6c-1.4 1.4-3.6 1.6-5.3.6-5-3-8.9-6.9-11.9-11.9-1-1.7-.8-3.9.6-5.3z" fill="#fff"/>
      </svg>
      <svg viewBox="0 0 42 42" aria-label="Email">
        <circle cx="21" cy="21" r="21" fill="var(--icon)"/>
        <rect x="10" y="13" width="22" height="16" rx="2" fill="#fff"/>
        <path d="M10.5 14l10.5 8.5 10.5-8.5" fill="none" stroke="var(--icon)" stroke-width="1.8"/>
      </svg>
      <svg viewBox="0 0 42 42" aria-label="Website">
        <circle cx="21" cy="21" r="21" fill="var(--icon)"/>
        <circle cx="21" cy="21" r="11" fill="none" stroke="#fff" stroke-width="2.4"/>
        <ellipse cx="21" cy="21" rx="4.5" ry="11" fill="none" stroke="#fff" stroke-width="2"/>
        <path d="M10 21h22" stroke="#fff" stroke-width="2"/>
      </svg>
      <span class="rule"></span>
    </div>

    <ul class="contact-details">
      <li class="phone">555-382-7194</li>
      <li class="email">email@lightfortheweary-mail.org</li>
      <li class="website">www.lightforthewearysouls.org</li>
    </ul>
  </main>
</body>
</html>
```